The Neighbors Together Project

For submission to Lantern Campaign 2024
Need both Color and Black and White Versions
TITLE The Neighbors Together Project
Slogan; "Neighbors Together, one road...one Heart, just a different stride" -JT Pellow copyrights
Logo in Color and Logo in Black and White
Back of flyer will be The Field of Quiet Lanterns poem -JT Pellow
VOTE BLUE 2024 Header or Footer

I just want to thank you all for your participation in The Neighbors Together Project. In the next few days I will be reducing the choices down to 10. Id like for all of you to know Ive enjoyed seeing so many options and views on the Flyer. Mainly, I wanted to say to those who don't make the cut that I appreciate the work you've done.

LM Dorsey

```html
<!DOCTYPE html>
<html lang="en">
<head>
<meta charset="utf-8">
<title>The Neighbors Together Project – Flyer</title>
<link href="https://fonts.googleapis.com/css2?family=Bebas+Neue&family=Passion+One:wght@700&family=Poppins:wght@400;500;600&display=swap" rel="stylesheet">
<style>
  :root {
    --backdrop: #7d7a79;
    --paper: #ffffff;
    --navy: #1c1f45;
    --navy-deep: #15183a;
    --royal: #2a43a3;
    --title-dark: #26284a;
    --red: #e53a3a;
    --red-deep: #c3272d;
    --ink: #1a1a1a;
    --drape-red: #f3c9cf;
    --drape-blue: #c9d2e6;
  }
  * { box-sizing: border-box; margin: 0; padding: 0; }
  html, body { width: 1200px; height: 835px; overflow: hidden; }
  body { background: var(--backdrop); position: relative; font-family: "Poppins", sans-serif; }

  .flyer {
    position: absolute; top: 135px; width: 435px; height: 562px;
    background: var(--paper); overflow: hidden;
  }
  .flyer--front { left: 125px; }
  .flyer--back { left: 643px; }

  .drape { position: absolute; top: 0; left: 0; width: 435px; height: 180px; }

  /* Front */
  .brand-mark {
    position: absolute; top: 52px; left: 0; width: 100%;
    display: flex; align-items: center; justify-content: center; gap: 8px;
    font-family: "Poppins", sans-serif; font-weight: 600; font-size: 13px;
    color: var(--title-dark); letter-spacing: 0.5px;
  }
  .brand-mark .dot { width: 14px; height: 14px; border-radius: 50%; background: var(--royal); }

  .project-title {
    position: absolute; top: 138px; width: 100%; text-align: center;
    font-family: "Passion One", sans-serif; font-weight: 700; line-height: 0.92;
    font-size: 37px; text-transform: uppercase;
  }
  .project-title .line-1 { display: block; color: var(--royal); }
  .project-title .line-2 { display: block; color: var(--title-dark); }

  .flag-wave { position: absolute; left: 0; top: 190px; width: 435px; height: 372px; }

  .slogan { position: absolute; top: 345px; width: 100%; text-align: center; }
  .slogan__lead {
    font-family: "Poppins", sans-serif; font-weight: 500; color: #fff;
    font-size: 21px; letter-spacing: 5px; line-height: 1;
  }
  .slogan__big {
    font-family: "Bebas Neue", sans-serif; color: var(--red);
    font-size: 66px; line-height: 0.8; margin-top: 10px;
  }
  .slogan__tail {
    font-family: "Bebas Neue", sans-serif; color: #fff;
    font-size: 30px; line-height: 1; margin-top: 6px;
  }
  .credit-badge {
    display: inline-block; margin-top: 6px; background: var(--royal); color: #fff;
    font-family: "Poppins", sans-serif; font-weight: 600; font-size: 9.5px;
    letter-spacing: 1.6px; padding: 2px 8px; line-height: 11px;
  }

  /* Back */
  .poem-title {
    position: absolute; top: 35px; width: 100%; text-align: center;
    font-family: "Passion One", sans-serif; font-weight: 700; color: var(--royal);
    font-size: 46px; line-height: 0.92; text-transform: uppercase;
  }
  .poem-author {
    position: absolute; top: 123px; width: 100%; text-align: center;
    font-family: "Poppins", sans-serif; font-weight: 600; color: var(--ink);
    font-size: 14px; letter-spacing: 2.5px;
  }
  .poem {
    position: absolute; top: 170px; left: 50px; width: 335px; text-align: center;
    font-size: 10.6px; line-height: 12.8px; color: var(--ink);
  }
  .poem p + p { margin-top: 12.5px; }
  .divider { position: absolute; top: 412px; left: 208px; width: 18px; height: 3px; background: var(--ink); }
  .site-url {
    position: absolute; top: 434px; width: 100%; text-align: center;
    font-size: 13px; letter-spacing: 1.6px; color: var(--ink);
  }
  .site-url strong { color: var(--royal); font-weight: 600; }
  .vote-line {
    position: absolute; top: 466px; width: 100%; text-align: center;
    font-family: "Bebas Neue", sans-serif; font-size: 80px; line-height: 1;
    color: var(--royal);
  }
  .vote-line .year { color: var(--red-deep); }
</style>
</head>
<body>

<section class="flyer flyer--front">
  <svg class="drape" viewBox="0 0 435 180" role="img" aria-label="Faded draped flag corners">
    <defs>
      <linearGradient id="drapeL" x1="0" y1="0" x2="1" y2="1">
        <stop offset="0" stop-color="var(--drape-blue)"/>
        <stop offset="0.45" stop-color="var(--drape-red)" stop-opacity="0.7"/>
        <stop offset="1" stop-color="#fff" stop-opacity="0"/>
      </linearGradient>
      <linearGradient id="drapeR" x1="1" y1="0" x2="0" y2="1">
        <stop offset="0" stop-color="var(--drape-blue)"/>
        <stop offset="0.45" stop-color="var(--drape-red)" stop-opacity="0.7"/>
        <stop offset="1" stop-color="#fff" stop-opacity="0"/>
      </linearGradient>
    </defs>
    <path d="M0 0 H150 C120 40 80 90 0 150 Z" fill="url(#drapeL)"/>
    <path d="M435 0 H285 C315 40 355 90 435 150 Z" fill="url(#drapeR)"/>
  </svg>

  <div class="brand-mark"><span class="dot"></span>The Neighbors Together Project</div>

  <h1 class="project-title">
    <span class="line-1">The Neighbors</span>
    <span class="line-2">Together Project</span>
  </h1>

  <svg class="flag-wave" viewBox="0 0 435 372" preserveAspectRatio="none">
    <defs>
      <linearGradient id="flagTone" x1="0" y1="0" x2="1" y2="0">
        <stop offset="0" stop-color="#2b2f6e"/>
        <stop offset="0.28" stop-color="#e8384f"/>
        <stop offset="0.5" stop-color="#f7d3d8"/>
        <stop offset="0.75" stop-color="#e8384f"/>
        <stop offset="1" stop-color="#f0a0ac"/>
      </linearGradient>
    </defs>
    <path d="M0 58 C70 40 110 30 170 70 C240 115 300 90 435 0 V372 H0 Z" fill="var(--navy)"/>
    <path role="img" aria-label="Waving flag banner"
          d="M0 58 C60 45 100 25 170 55 C240 85 300 60 435 -2 V12 C330 70 270 130 190 110 C130 95 60 100 0 130 Z"
          fill="url(#flagTone)"/>
  </svg>

  <div class="slogan">
    <p class="slogan__lead">NEIGHBORS TOGETHER</p>
    <p class="slogan__big">One Road...<br>One Heart,</p>
    <p class="slogan__tail">Just A Different Stride</p>
    <span class="credit-badge">JT PELLOW COPYRIGHTS©</span>
  </div>
</section>

<section class="flyer flyer--back">
  <svg class="drape" viewBox="0 0 435 180" role="img" aria-label="Faded draped flag corners">
    <defs>
      <linearGradient id="drapeL2" x1="0" y1="0" x2="1" y2="1">
        <stop offset="0" stop-color="var(--drape-blue)"/>
        <stop offset="0.45" stop-color="var(--drape-red)" stop-opacity="0.7"/>
        <stop offset="1" stop-color="#fff" stop-opacity="0"/>
      </linearGradient>
      <linearGradient id="drapeR2" x1="1" y1="0" x2="0" y2="1">
        <stop offset="0" stop-color="var(--drape-blue)"/>
        <stop offset="0.45" stop-color="var(--drape-red)" stop-opacity="0.7"/>
        <stop offset="1" stop-color="#fff" stop-opacity="0"/>
      </linearGradient>
    </defs>
    <path d="M0 0 H150 C120 40 80 90 0 160 Z" fill="url(#drapeL2)"/>
    <path d="M435 0 H285 C315 40 355 90 435 160 Z" fill="url(#drapeR2)"/>
  </svg>

  <h2 class="poem-title">Field of<br>Quiet Lanterns</h2>
  <p class="poem-author">BY JT PELLOW</p>

  <div class="poem">
    <p>From harvest roads at twilight to the porches far from town,<br>we set our little lanterns out as evening settles down.</p>
    <p>We are a field of quiet lights...amber, gold and pale and bright,<br>each one a different glow, yet all one against the night.</p>
    <p>We have come from many places, crossed the rivers and the plains. Leaving homes and old companions...through the sunshine and the rains.</p>
    <p>Free to speak, Free to gather, Free to wander or to rest...working, building side by side on this road we know is best.</p>
    <p>We must always keep them burning, lend a hand to those who call.<br>For together we shine brighter, but alone the shadows fall.</p>
  </div>

  <div class="divider"></div>
  <p class="site-url">www.<strong>neighborstogetherhub</strong>.org</p>
  <p class="vote-line">Vote Blue <span class="year">2024</span></p>
</section>

</body>
</html>
```